I need an Office Furniture selling website

My office furniture store is driven by creativity and innovation. With this i am searching for an industry standard website for my office furniture and items selling website. I sell a wide range of office furniture items such as chairs, tables, burglary, cotton, wardrobe, etc. There will be a category for each of the items i sell. My business is based in the United States and services only US based residents. I don't accept online payments and customers are to pay on delivery of items. The website is to have images of the items i sell. I would like brown, black and golden colors because those are the colors furniture mostly make use of. Designs submitted should be unique.

Industry/Entity Type

Furniture Store

Coding

Coded - Design and coding required

```html
<!DOCTYPE html>
<html lang="en">
<head>
<meta charset="utf-8">
<title>Corvane Office Furniture</title>
<link rel="stylesheet" href="https://fonts.googleapis.com/css2?family=Oswald:wght@400;500&family=Roboto:wght@400;500;700&display=swap">
<style>
:root{
  --gold:#f5b42a;
  --gold-dark:#e39d12;
  --brown:#6c2d18;
  --brown-accent:#7b3416;
  --ink:#222222;
  --muted:#666666;
  --soft:#ececec;
  --line:#e2e2e2;
  --night:#1d1d1d;
  --price:#e2303a;
}
*{box-sizing:border-box;margin:0;padding:0}
html,body{width:1200px;height:3109px;overflow:hidden}
body{font-family:"Roboto",Arial,sans-serif;color:var(--ink);background:#fff;position:relative}
.abs{position:absolute}

/* top bar */
.topbar{position:absolute;left:0;top:0;width:1200px;height:46px;background:var(--brown);color:#fff;font-size:12px}
.topbar .contact{position:absolute;left:90px;top:15px;display:flex;gap:30px;align-items:center}
.topbar .contact span{display:flex;align-items:center;gap:8px}
.topbar .account{position:absolute;right:86px;top:15px;display:flex;gap:14px}
.topbar .account i{font-style:normal;opacity:.8}

/* header */
.header{position:absolute;left:0;top:46px;width:1200px;height:95px;background:#fff}
.brand{position:absolute;left:89px;top:30px;display:flex;align-items:center;gap:12px;font-family:"Oswald",sans-serif;font-size:31px;font-weight:500;color:var(--ink);line-height:1}
.brand .mark{width:36px;height:34px;background:var(--gold)}
.nav{position:absolute;right:90px;top:41px;display:flex;gap:34px;font-size:13px;text-transform:uppercase;color:#333}
.nav .active{color:var(--gold)}

/* hero */
.hero{position:absolute;left:0;top:141px;width:1200px;height:543px}
.hero .photo{position:absolute;inset:0;background:linear-gradient(120deg,#3a2a22 0%,#8d6f55 30%,#d9c7ad 55%,#5a3b2b 80%,#2e2320 100%)}
.hero .caption{position:absolute;left:87px;top:390px;width:400px;height:108px;background:rgba(40,40,40,.72);padding:14px 24px;color:#fff;font-family:"Oswald",sans-serif}
.hero .caption h2{font-size:32px;font-weight:400;line-height:1.15}
.hero .caption p{font-size:28px;font-weight:400;line-height:1.15;opacity:.95}
.hero .arrows{position:absolute;left:1055px;top:466px;display:flex;gap:4px}
.arrow-btn{width:26px;height:36px;background:rgba(40,40,40,.85);border:1px solid #aaa;display:flex;align-items:center;justify-content:center}

/* section titles */
.title{font-size:25px;font-weight:500;text-transform:uppercase;color:var(--ink);letter-spacing:.3px}
.title b{font-weight:500;color:var(--brown-accent)}
.center{text-align:center;width:1200px;left:0}

/* welcome */
.welcome .title{position:absolute;top:734px;font-size:31px}
.welcome p{position:absolute;left:190px;top:782px;width:820px;text-align:center;font-size:15px;line-height:24px;color:var(--muted)}

/* category */
.category{position:absolute;left:0;top:879px;width:1200px;height:423px;background:var(--soft)}
.category .title{position:absolute;top:43px}
.cat-card{position:absolute;top:106px;width:249px;height:253px;background:#fff;box-shadow:0 2px 4px rgba(0,0,0,.18)}
.cat-card .pic{height:157px}
.cat-card h3{text-align:center;font-size:14px;font-weight:400;margin-top:22px;text-transform:uppercase}
.btn-pill{display:block;margin:8px auto 0;width:104px;height:27px;border-radius:14px;background:var(--gold);color:#fff;font-size:9px;text-transform:uppercase;text-align:center;line-height:27px;box-shadow:0 2px 0 var(--gold-dark)}

/* promo */
.promo{position:absolute;left:0;top:1302px;width:1200px;height:415px;overflow:hidden}
.promo .photo{position:absolute;inset:0;background:linear-gradient(90deg,#bfb6ae 0%,#e9e6e2 45%,#c9a17a 70%,#f1efec 100%)}
.promo .shade{position:absolute;inset:0}
.promo .copy{position:absolute;left:116px;top:48px;color:#fff}
.promo h2{font-size:28px;font-weight:500;text-transform:uppercase}
.promo h4{font-size:18px;font-weight:500;margin-top:8px}
.promo ul{list-style:none;margin-top:14px}
.promo li{font-size:15px;line-height:30px;display:flex;align-items:center;gap:10px}
.promo .cta{display:block;margin-top:14px;width:230px;height:42px;border-radius:21px;background:var(--gold);color:#fff;font-size:13px;text-transform:uppercase;text-align:center;line-height:42px}

/* featured */
.featured .title{position:absolute;left:87px;top:1780px}
.featured .nav-arrows{position:absolute;left:1083px;top:1785px;display:flex;gap:6px}
.prod{position:absolute;top:1839px;width:242px;height:334px;border:1px solid var(--line);background:#fff}
.prod .pic{height:209px;display:flex;align-items:center;justify-content:center}
.prod .pic div{width:140px;height:170px;border-radius:6px}
.prod .name{height:38px;background:#f1f1f1;text-align:center;font-size:15px;line-height:38px;color:#444}
.prod .price{text-align:center;font-size:18px;margin-top:8px;color:var(--price)}
.prod .price s{font-size:12px;color:#999;margin-right:10px}
.prod .actions{position:absolute;left:-1px;right:-1px;bottom:-1px;height:44px;display:flex;border-top:1px solid var(--line)}
.prod .actions span{flex:1;display:flex;align-items:center;justify-content:center;border-left:1px solid var(--line)}
.prod .actions span:first-child{background:var(--gold);border-left:none}

/* store band */
.store{position:absolute;left:0;top:2239px;width:1200px;height:276px;background:linear-gradient(180deg,#1a1a1a,#2c2622 60%,#1c1a19);color:#fff;text-align:center}
.store h2{margin-top:58px;font-size:31px;font-weight:500;text-transform:uppercase}
.store p{width:860px;margin:14px auto 0;font-size:17px;line-height:29px}
.store .cta{display:block;margin:20px auto 0;width:176px;height:44px;border-radius:22px;background:var(--gold);font-size:19px;line-height:44px}

/* partners */
.partners .title{position:absolute;top:2588px;font-size:24px}
.partner{position:absolute;top:2676px;height:38px;background:#c9c9c9;border-radius:3px}

/* footer */
.footer{position:absolute;left:0;top:2795px;width:1200px;height:221px;background:var(--brown);color:#fff}
.footer h5{font-size:14px;font-weight:500;text-transform:uppercase;margin-bottom:14px}
.footer .col{position:absolute;top:45px;font-size:11.5px;line-height:19px}
.footer input{display:block;width:215px;height:30px;border:none;padding:0 8px;font-size:11px;margin-top:10px;font-family:inherit}
.footer .sub{display:block;margin-top:12px;width:94px;height:28px;background:var(--gold);text-align:center;line-height:28px;font-size:10px;text-transform:uppercase}
.footer .social li{list-style:none;display:flex;align-items:center;gap:14px;height:43px;font-size:12px}
.footer .social .dot{width:34px;height:34px;border-radius:50%;border:1px solid rgba(255,255,255,.6)}
.bottombar{position:absolute;left:0;top:3016px;width:1200px;height:93px;background:var(--night);color:#fff}
.bottombar .pay{position:absolute;left:89px;top:29px;width:62px;height:42px;background:#f2f2f2;border-radius:4px}
.bottombar .copy{position:absolute;right:88px;top:40px;font-size:11px}
</style>
</head>
<body>

<div class="topbar">
  <div class="contact">
    <span><svg width="11" height="11" viewBox="0 0 24 24"><path fill="#fff" d="M6.6 10.8a15 15 0 0 0 6.6 6.6l2.2-2.2c.3-.3.7-.4 1-.2 1.1.4 2.3.6 3.6.6.6 0 1 .4 1 1V20c0 .6-.4 1-1 1A17 17 0 0 1 3 4c0-.6.4-1 1-1h3.5c.6 0 1 .4 1 1 0 1.3.2 2.5.6 3.6.1.3 0 .7-.2 1z"/></svg>555-013-2840</span>
    <span><svg width="10" height="13" viewBox="0 0 20 26"><path fill="#fff" d="M10 0a9 9 0 0 0-9 9c0 7 9 17 9 17s9-10 9-17a9 9 0 0 0-9-9zm0 12.5A3.5 3.5 0 1 1 10 5.5a3.5 3.5 0 0 1 0 7z"/></svg>Find our Address</span>
  </div>
  <div class="account"><span>Sign In or Register</span><i>|</i><span>My Account</span><i>|</i><span>Selling</span></div>
</div>

<header class="header">
  <div class="brand"><span class="mark"></span>CORVANE</div>
  <nav class="nav"><span class="active">Home</span><span>About Us</span><span>Products</span><span>Furnitures</span><span>Category</span><span>Blog</span><span>Contact Us</span></nav>
</header>

<section class="hero">
  <div class="photo" role="img" aria-label="Executive office with dark wood desk, black leather chairs and cabinets"></div>
  <div class="caption"><h2>OFFICE FURNITURE SELLING</h2><p>Neque porro quisquam est qui</p></div>
  <div class="arrows">
    <span class="arrow-btn"><svg width="10" height="16" viewBox="0 0 10 16"><path d="M8 2 2 8l6 6" stroke="#fff" stroke-width="2" fill="none"/></svg></span>
    <span class="arrow-btn"><svg width="10" height="16" viewBox="0 0 10 16"><path d="m2 2 6 6-6 6" stroke="#fff" stroke-width="2" fill="none"/></svg></span>
  </div>
</section>

<section class="welcome">
  <h2 class="title abs center">Welcome to <b>Corvane</b></h2>
  <p>Lorem Ipsum has been the industry's standard dummy text ever since the 1500s, when an unknown printer took a galley of type and scrambled it to make a type specimen book.</p>
</section>

<section class="category">
  <h2 class="title abs center">Select <b>Category</b></h2>
  <div class="cat-card" style="left:87px"><div class="pic" role="img" aria-label="Office with executive chairs" style="background:linear-gradient(135deg,#d8d2cb,#5a3a2c 60%,#2b2220)"></div><h3>Chairs</h3><span class="btn-pill">Book Now</span></div>
  <div class="cat-card" style="left:346px"><div class="pic" role="img" aria-label="Light wood office table" style="background:linear-gradient(180deg,#eeeae4,#c9a57a 65%,#b58b5c)"></div><h3>Tables</h3><span class="btn-pill">Book Now</span></div>
  <div class="cat-card" style="left:605px"><div class="pic" role="img" aria-label="White office workstations" style="background:linear-gradient(180deg,#e6e6e6,#fafafa 55%,#9a9a9a)"></div><h3>Burglary</h3><span class="btn-pill">Book Now</span></div>
  <div class="cat-card" style="left:864px"><div class="pic" role="img" aria-label="Open plan office with storage" style="background:linear-gradient(180deg,#f0f3f5,#dfe4e8 50%,#a89884)"></div><h3>Wardrobe</h3><span class="btn-pill">Book Now</span></div>
</section>

<section class="promo">
  <div class="photo" role="img" aria-label="Modern office with wooden desk, lamp and black chair"></div>
  <svg class="shade" width="1200" height="415" viewBox="0 0 1200 415"><polygon points="0,0 705,0 470,415 0,415" fill="rgba(28,24,22,.88)"/></svg>
  <div class="copy">
    <h2>Office Furniture Selling</h2>
    <h4>Neque porro quisquam est qui dolorem ipsum</h4>
    <ul>
      <li><svg width="10" height="10" viewBox="0 0 10 10"><path d="M1 1l4 4-4 4M5 1l4 4-4 4" stroke="#fff" stroke-width="1.5" fill="none"/></svg>Ipsum is simply dummy text of the printing</li>
      <li><svg width="10" height="10" viewBox="0 0 10 10"><path d="M1 1l4 4-4 4M5 1l4 4-4 4" stroke="#fff" stroke-width="1.5" fill="none"/></svg>Porro quisquam est qui dolorem ipsum quia</li>
      <li><svg width="10" height="10" viewBox="0 0 10 10"><path d="M1 1l4 4-4 4M5 1l4 4-4 4" stroke="#fff" stroke-width="1.5" fill="none"/></svg>It has survived not only five centuries</li>
      <li><svg width="10" height="10" viewBox="0 0 10 10"><path d="M1 1l4 4-4 4M5 1l4 4-4 4" stroke="#fff" stroke-width="1.5" fill="none"/></svg>Ipsum is simply dummy text of the printing</li>
      <li><svg width="10" height="10" viewBox="0 0 10 10"><path d="M1 1l4 4-4 4M5 1l4 4-4 4" stroke="#fff" stroke-width="1.5" fill="none"/></svg>Porro quisquam est qui dolorem ipsum quia</li>
      <li><svg width="10" height="10" viewBox="0 0 10 10"><path d="M1 1l4 4-4 4M5 1l4 4-4 4" stroke="#fff" stroke-width="1.5" fill="none"/></svg>It has survived not only five centuries</li>
    </ul>
    <span class="cta">Choose Your Furniture</span>
  </div>
</section>

<section class="featured">
  <h2 class="title">Featured <b>Products</b></h2>
  <div class="nav-arrows">
    <svg width="12" height="18" viewBox="0 0 12 18"><path d="M10 2 3 9l7 7" stroke="#333" stroke-width="2.5" fill="none"/></svg>
    <svg width="12" height="18" viewBox="0 0 12 18"><path d="m2 2 7 7-7 7" stroke="#333" stroke-width="2.5" fill="none"/></svg>
  </div>
  <div class="prod" style="left:83px"><div class="pic"><div role="img" aria-label="Black leather office chair" style="background:linear-gradient(180deg,#3a3a3a,#1a1a1a 70%,#8a5a3a)"></div></div><div class="name">Lorem ipsum dolor</div><div class="price"><s>$160.00</s>$ 150.00</div>
    <div class="actions"><span><svg width="18" height="16" viewBox="0 0 18 16"><path d="M1 1h3l2 9h9l2-6H5" stroke="#fff" stroke-width="1.8" fill="none"/><circle cx="7" cy="14" r="1.5" fill="#fff"/><circle cx="14" cy="14" r="1.5" fill="#fff"/></svg></span><span><svg width="15" height="13" viewBox="0 0 16 14"><path d="M8 13 2 7a3.5 3.5 0 0 1 6-4 3.5 3.5 0 0 1 6 4z" fill="#aaa"/></svg></span><span><svg width="16" height="14" viewBox="0 0 16 14"><path d="M1 4h12l-3-3M15 10H3l3 3" stroke="#aaa" stroke-width="1.8" fill="none"/></svg></span><span><svg width="15" height="15" viewBox="0 0 16 16"><circle cx="8" cy="8" r="6.5" stroke="#aaa" stroke-width="1.6" fill="none"/><path d="M8 4v4h3" stroke="#aaa" stroke-width="1.6" fill="none"/></svg></span></div></div>
  <div class="prod" style="left:344px"><div class="pic"><div role="img" aria-label="Light wood drawer cabinet" style="background:linear-gradient(180deg,#2a2a2a 0 8%,#f1c48f 8%,#e3ab70)"></div></div><div class="name">Lorem ipsum dolor</div><div class="price"><s>$160.00</s>$ 150.00</div>
    <div class="actions"><span><svg width="18" height="16" viewBox="0 0 18 16"><path d="M1 1h3l2 9h9l2-6H5" stroke="#fff" stroke-width="1.8" fill="none"/><circle cx="7" cy="14" r="1.5" fill="#fff"/><circle cx="14" cy="14" r="1.5" fill="#fff"/></svg></span><span><svg width="15" height="13" viewBox="0 0 16 14"><path d="M8 13 2 7a3.5 3.5 0 0 1 6-4 3.5 3.5 0 0 1 6 4z" fill="#aaa"/></svg></span><span><svg width="16" height="14" viewBox="0 0 16 14"><path d="M1 4h12l-3-3M15 10H3l3 3" stroke="#aaa" stroke-width="1.8" fill="none"/></svg></span><span><svg width="15" height="15" viewBox="0 0 16 16"><circle cx="8" cy="8" r="6.5" stroke="#aaa" stroke-width="1.6" fill="none"/><path d="M8 4v4h3" stroke="#aaa" stroke-width="1.6" fill="none"/></svg></span></div></div>
  <div class="prod" style="left:605px"><div class="pic"><div role="img" aria-label="Tan leather swivel chair" style="background:linear-gradient(180deg,#c0552a,#a13f1c 65%,#555)"></div></div><div class="name">Lorem ipsum dolor</div><div class="price"><s>$160.00</s>$ 150.00</div>
    <div class="actions"><span><svg width="18" height="16" viewBox="0 0 18 16"><path d="M1 1h3l2 9h9l2-6H5" stroke="#fff" stroke-width="1.8" fill="none"/><circle cx="7" cy="14" r="1.5" fill="#fff"/><circle cx="14" cy="14" r="1.5" fill="#fff"/></svg></span><span><svg width="15" height="13" viewBox="0 0 16 14"><path d="M8 13 2 7a3.5 3.5 0 0 1 6-4 3.5 3.5 0 0 1 6 4z" fill="#aaa"/></svg></span><span><svg width="16" height="14" viewBox="0 0 16 14"><path d="M1 4h12l-3-3M15 10H3l3 3" stroke="#aaa" stroke-width="1.8" fill="none"/></svg></span><span><svg width="15" height="15" viewBox="0 0 16 16"><circle cx="8" cy="8" r="6.5" stroke="#aaa" stroke-width="1.6" fill="none"/><path d="M8 4v4h3" stroke="#aaa" stroke-width="1.6" fill="none"/></svg></span></div></div>
  <div class="prod" style="left:868px"><div class="pic"><div role="img" aria-label="Wooden coffee table" style="width:200px;height:120px;background:linear-gradient(180deg,#d07a40,#b25e2a 60%,#8a4520)"></div></div><div class="name">Lorem ipsum dolor</div><div class="price"><s>$160.00</s>$ 150.00</div>
    <div class="actions"><span><svg width="18" height="16" viewBox="0 0 18 16"><path d="M1 1h3l2 9h9l2-6H5" stroke="#fff" stroke-width="1.8" fill="none"/><circle cx="7" cy="14" r="1.5" fill="#fff"/><circle cx="14" cy="14" r="1.5" fill="#fff"/></svg></span><span><svg width="15" height="13" viewBox="0 0 16 14"><path d="M8 13 2 7a3.5 3.5 0 0 1 6-4 3.5 3.5 0 0 1 6 4z" fill="#aaa"/></svg></span><span><svg width="16" height="14" viewBox="0 0 16 14"><path d="M1 4h12l-3-3M15 10H3l3 3" stroke="#aaa" stroke-width="1.8" fill="none"/></svg></span><span><svg width="15" height="15" viewBox="0 0 16 16"><circle cx="8" cy="8" r="6.5" stroke="#aaa" stroke-width="1.6" fill="none"/><path d="M8 4v4h3" stroke="#aaa" stroke-width="1.6" fill="none"/></svg></span></div></div>
</section>

<section class="store" role="img" aria-label="Dimmed office interior behind the message">
  <h2>Welcome to our store</h2>
  <p>Lorem Ipsum has been the industry's standard dummy text ever since the 1500s, when an unknown printer took a galley of type and scrambled it to make a type specimen book.</p>
  <span class="cta">Book Now</span>
</section>

<section class="partners">
  <h2 class="title abs center">Our Partners</h2>
  <span class="partner" style="left:141px;width:68px"></span>
  <span class="partner" style="left:265px;width:118px"></span>
  <span class="partner" style="left:442px;width:97px"></span>
  <span class="partner" style="left:609px;width:112px"></span>
  <span class="partner" style="left:806px;width:85px"></span>
  <span class="partner" style="left:964px;width:120px"></span>
</section>

<footer class="footer">
  <div class="col" style="left:87px;width:230px">
    <h5>Newsletters Sign Up</h5>
    Sign up for our daily email by entering your information below
    <input type="text" placeholder="Email address">
    <span class="sub">Subscribe</span>
  </div>
  <div class="col" style="left:386px;width:230px">
    <h5>Corvane</h5>
    <p style="text-align:justify;padding-left:8px">Lorem Ipsum has been the industry's standard dummy text ever since the 1500s, when an unknown printer took a galley of type and scrambled it to make a type specimen book.</p>
  </div>
  <div class="col" style="left:699px;width:230px;line-height:26px">
    <h5 style="margin-bottom:6px">Get in Touch</h5>
    Address : 1200 Elm Ridge Ave,<br>Maple Falls, NJ<br>Phone : 201 555 0147<br>Email : info@corvane-office.com
  </div>
  <div class="col social" style="left:960px;width:180px">
    <h5 style="margin-bottom:6px">Follow Us On</h5>
    <ul><li><span class="dot"></span>Linkwall</li><li><span class="dot"></span>Chatterly</li><li><span class="dot"></span>Photofeed</li></ul>
  </div>
</footer>

<div class="bottombar">
  <span class="pay"></span>
  <span class="copy">Copyright © 2016 &nbsp;All Rights Reserved</span>
</div>

</body>
</html>
```